Wendtal Storen
Zielgruppe
Storenbau: Lammellenstoren, Markisen, Beschattungen, Klappläden
Service: Reparatur und Unterhalt bestehender Anlagen
Aufgabenstellung
Klare Linen / wenig Schnörkel
Briefpapier: ein schwacher, Wasserzeichen-ähnlicher Schriftzug seitlich/unten am rechten Rand würde uns gefallen...
Die Farbe Azurblau RAL5009 (oder ähnlich) haben wir in Erwägung gezogen ...

```html
<!DOCTYPE html>
<html lang="de">
<head>
<meta charset="utf-8">
<title>Wendtal Storenbau GmbH – Corporate Design</title>
<link href="https://fonts.googleapis.com/css2?family=Exo+2:wght@400;500;600&display=swap" rel="stylesheet">
<style>
  :root{
    --azure:#2b6192;
    --grey:#b4b4b4;
    --grey-dark:#9e9e9e;
    --paper:#ffffff;
    --bg:#ebebeb;
    --ink:#4a4a4a;
    --faint:#f3f3f3;
    --faint-dark:#dedede;
  }
  *{box-sizing:border-box;margin:0;padding:0}
  html,body{width:893px;height:1200px;overflow:hidden}
  body{position:relative;background:var(--bg);font-family:"Exo 2",sans-serif;color:var(--ink)}
  .abs{position:absolute}

  .hero{left:0;top:0;width:893px;height:252px;background:radial-gradient(ellipse at 50% 40%,#ffffff 0%,#f3f3f3 60%,#e9e9e9 100%)}
  .hero-badge{left:798px;top:27px;width:60px;height:52px;background:#f4f4f4;box-shadow:0 1px 4px rgba(0,0,0,.18)}

  .band-blue{left:0;top:252px;width:446px;height:149px;background:var(--azure)}
  .band-grey{left:446px;top:252px;width:447px;height:149px;background:var(--grey)}

  /* wordmark */
  .logo{position:absolute;display:flex;align-items:center;gap:.7em;color:var(--azure);font-weight:600;text-transform:uppercase}
  .logo-mark{width:2.3em;height:2.3em;background:currentColor;flex:none}
  .logo-name{line-height:1.15;letter-spacing:.55em;white-space:nowrap}
  .logo-name span{display:block}
  .logo--white{color:#fff}
  .logo--faint{color:var(--faint-dark)}
  .logo--ghost{color:#f7f7f7}

  .sheet{background:var(--paper);box-shadow:0 1px 4px rgba(0,0,0,.15)}
  .letter{left:12px;top:439px;width:444px;height:628px}
  .letter-rule{left:0;bottom:0;width:100%;height:5px;background:var(--azure)}
  .letter-sender{left:48px;top:100px;font-size:5.5px}
  .letter-contact{left:347px;top:98px;font-size:7.5px;line-height:1.2}
  .letter-contact p{margin-bottom:5px}
  .link{color:var(--azure)}
  .letter-watermark{left:140px;top:235px;width:187px;height:157px;background:var(--faint)}
  .letter-bank{left:334px;top:557px;font-size:7.5px;line-height:1.15}
  .letter-bank p{margin-bottom:7px}

  .card{width:200px;height:111px}
  .card-name{font-size:9px;font-weight:500;color:var(--azure);text-align:center;line-height:1}
  .card-pos{display:block;font-size:5.5px;letter-spacing:.15em;margin-top:1px;font-weight:600}
  .card-bar{left:0;top:48px;width:100%;height:25px;background:var(--azure);color:#fff;padding-top:5px}
  .card-bar .card-name{color:#fff}
  .card-addr{font-size:5px;line-height:1.3}
  .card-ghost{left:0;top:47px;width:75px;height:64px;background:var(--faint)}
  .card-blue{background:var(--azure)}

  .envelope{left:505px;top:816px;width:337px;height:274px;border-radius:8px 8px 0 0;overflow:hidden}
  .env-flap{left:0;top:0;width:100%;height:61px;background:var(--grey-dark)}
  .env-mark{left:155px;top:19px;width:25px;height:21px;background:var(--azure)}
  .env-base{left:0;bottom:0;width:100%;height:3px;background:var(--grey-dark)}
</style>
</head>
<body>

<section class="abs hero" aria-label="Hauptlogo">
  <div class="logo" style="font-size:27px;left:200px;top:96px">
    <div class="logo-mark"></div>
    <div class="logo-name"><span>Wendtal</span><span>Storenbau GmbH</span></div>
  </div>
  <div class="abs hero-badge"></div>
</section>

<section class="abs band-blue">
  <div class="logo logo--white" style="font-size:18px;left:48px;top:53px">
    <div class="logo-mark"></div>
    <div class="logo-name"><span>Wendtal</span><span>Storenbau GmbH</span></div>
  </div>
</section>
<section class="abs band-grey">
  <div class="logo" style="font-size:18px;left:47px;top:53px">
    <div class="logo-mark"></div>
    <div class="logo-name"><span>Wendtal</span><span>Storenbau GmbH</span></div>
  </div>
</section>

<article class="abs sheet letter">
  <div class="logo" style="font-size:11px;left:215px;top:32px">
    <div class="logo-mark"></div>
    <div class="logo-name"><span>Wendtal</span><span>Storenbau GmbH</span></div>
  </div>
  <p class="abs letter-sender">WS | Musterserabe 1234 | 12345 Musterstredt</p>
  <div class="abs letter-contact">
    <p>Musterserabe 1234<br>12345 Musterstredt</p>
    <p>T:&nbsp; (+49) 123 45 678<br>F:&nbsp; (+49) 123 45 679</p>
    <p class="link">mail@wendtal-storen.ch<br>www.wendtal-storen.ch</p>
  </div>
  <div class="abs letter-watermark"></div>
  <div class="abs letter-bank">
    <p>Musterbank Musterstadt<br>DDD 123 123 123<br>BLZ 123 123 123</p>
    <p>Steuer-Nr. 123|1234|1234<br>USt-dNr. DE123456789</p>
  </div>
  <div class="abs letter-rule"></div>
</article>

<!-- card 1 -->
<article class="abs sheet card" style="left:467px;top:437px">
  <div class="logo" style="font-size:7px;left:24px;top:13px">
    <div class="logo-mark"></div>
    <div class="logo-name"><span>Wendtal</span><span>Storenbau GmbH</span></div>
  </div>
  <div class="abs card-bar"><p class="card-name">Max MUSTERMANN<span class="card-pos">POSITION</span></p></div>
  <p class="abs card-addr" style="left:23px;top:83px">Musterserabe 1234<br>12345 Musterstredt<br><span class="link">www.wendtal-storen.ch</span></p>
  <p class="abs card-addr" style="left:116px;top:83px">T:&nbsp; (+49) 123 45 678<br>F:&nbsp; (+49) 123 45 679<br>E:&nbsp; mail@wendtal-storen.ch</p>
</article>

<!-- card 2 -->
<article class="abs sheet card" style="left:679px;top:437px">
  <div class="logo" style="font-size:7px;left:20px;top:13px">
    <div class="logo-mark"></div>
    <div class="logo-name"><span>Wendtal</span><span>Storenbau GmbH</span></div>
  </div>
  <p class="abs card-name" style="left:22px;top:65px">Max MUSTERMANN<span class="card-pos" style="color:var(--ink)">POSITION</span></p>
  <p class="abs card-addr" style="left:126px;top:53px">Musterserabe 1234<br>12345 Musterstredt<br>www.wendtal-storen.ch</p>
  <p class="abs card-addr" style="left:126px;top:82px">T:&nbsp; (+49) 123 45 678<br>F:&nbsp; (+49) 123 45 679<br>E:&nbsp; mail@wendtal-storen.ch</p>
</article>

<!-- card 3 -->
<article class="abs sheet card" style="left:468px;top:560px">
  <div class="abs card-ghost"></div>
  <div class="logo" style="font-size:8px;left:16px;top:14px">
    <div class="logo-mark"></div>
    <div class="logo-name"><span>Wendtal</span><span>Storenbau GmbH</span></div>
  </div>
  <p class="abs card-name" style="left:83px;top:60px">Max MUSTERMANN<span class="card-pos">POSITION</span></p>
  <p class="abs card-addr" style="left:64px;top:85px">Musterserabe 1234<br>12345 Musterstredt<br>www.wendtal-storen.ch</p>
  <p class="abs card-addr" style="left:129px;top:85px">T:&nbsp; (+49) 123 45 678<br>F:&nbsp; (+49) 123 45 679<br>E:&nbsp; mail@wendtal-storen.ch</p>
</article>

<!-- card 4 -->
<article class="abs sheet card" style="left:681px;top:560px">
  <div class="logo" style="font-size:6.5px;left:23px;top:13px">
    <div class="logo-mark"></div>
    <div class="logo-name"><span>Wendtal</span><span>Storenbau GmbH</span></div>
  </div>
  <p class="abs card-name" style="left:0;width:100%;top:53px;color:#666">Max MUSTERMANN<span class="card-pos" style="color:var(--azure)">POSITION</span></p>
  <p class="abs card-addr" style="left:23px;top:82px">Musterserabe 1234<br>12345 Musterstredt<br><span class="link">www.wendtal-storen.ch</span></p>
  <p class="abs card-addr" style="left:116px;top:82px">T:&nbsp; (+49) 123 45 678<br>F:&nbsp; (+49) 123 45 679<br>E:&nbsp; mail@wendtal-storen.ch</p>
</article>

<!-- card backs -->
<article class="abs card card-blue" style="left:468px;top:683px">
  <div class="logo logo--white" style="font-size:6.5px;left:37px;top:47px">
    <div class="logo-mark"></div>
    <div class="logo-name"><span>Wendtal</span><span>Storenbau GmbH</span></div>
  </div>
</article>
<article class="abs sheet card" style="left:681px;top:683px">
  <div class="logo" style="font-size:6.5px;left:36px;top:48px">
    <div class="logo-mark"></div>
    <div class="logo-name"><span>Wendtal</span><span>Storenbau GmbH</span></div>
  </div>
</article>

<article class="abs sheet envelope">
  <div class="abs env-flap"></div>
  <div class="abs env-mark"></div>
  <div class="logo" style="font-size:8.5px;left:17px;top:232px">
    <div class="logo-mark"></div>
    <div class="logo-name"><span>Wendtal</span><span>Storenbau GmbH</span></div>
  </div>
  <div class="abs env-base"></div>
</article>

<div class="logo logo--faint" style="font-size:18px;left:54px;top:1128px">
  <div class="logo-mark"></div>
  <div class="logo-name"><span>Wendtal</span><span>Storenbau GmbH</span></div>
</div>
<div class="logo logo--ghost" style="font-size:18px;left:506px;top:1128px">
  <div class="logo-mark"></div>
  <div class="logo-name"><span>Wendtal</span><span>Storenbau GmbH</span></div>
</div>

</body>
</html>
```